Northfield Builders Guild Business card

We are looking for a new business card design with photo included.
Our business is a nonprofit construction contractor membership organization. We offer business education, assist with business setup and licensing, provide safety training, and provide a member directory.
URL: www.builderslinkguild.org
Color code:
CMYK: 0 cyan, 42 magenta, 100 yellow, 0 black for Print.
Hexidecimal: #FF9900
RGB: R 255; G 153; B 0

```html
<!DOCTYPE html>
<html lang="en">
<head>
<meta charset="utf-8">
<title>Northfield Builders Guild – Business Card</title>
<link rel="stylesheet" href="https://fonts.googleapis.com/css2?family=Arimo:wght@400;700&display=swap">
<style>
  :root {
    --bg: #2a2a2a;
    --card: #0d0d0d;
    --orange: #ff9900;
    --white: #ffffff;
    --rule: #4a4a4a;
  }
  * { box-sizing: border-box; margin: 0; padding: 0; }
  html, body { width: 1200px; height: 900px; overflow: hidden; }
  body {
    background: var(--bg);
    font-family: "Arimo", Arial, sans-serif;
    display: flex;
    align-items: center;
    justify-content: center;
    gap: 40px;
  }
  .card {
    width: 540px;
    height: 309px;
    background: var(--card);
    border-radius: 18px;
    position: relative;
    color: var(--white);
  }
  .brand {
    display: flex;
    align-items: center;
    gap: 10px;
    font-weight: 700;
    color: var(--white);
    text-transform: uppercase;
    line-height: 1.05;
  }
  .brand-dot {
    width: 16px; height: 16px; border-radius: 50%;
    background: var(--orange); flex: none;
  }
  /* front */
  .card-front .brand {
    position: absolute; left: 38px; top: 120px;
    font-size: 24px; width: 215px;
  }
  .card-front .divider {
    position: absolute; left: 262px; top: 60px;
    width: 1px; height: 190px; background: var(--rule);
  }
  .contact {
    position: absolute; left: 290px; top: 66px;
    font-size: 14px; line-height: 1.35;
  }
  .contact .name {
    color: var(--orange); font-weight: 700; font-size: 17px; text-transform: uppercase;
  }
  .contact .title { font-size: 11.5px; text-transform: uppercase; margin-bottom: 10px; }
  .contact .office { color: var(--orange); }
  .contact-row { display: flex; align-items: center; gap: 7px; margin-bottom: 2px; }
  .icon {
    width: 16px; height: 16px; border-radius: 50%;
    background: var(--orange); flex: none;
    display: flex; align-items: center; justify-content: center;
  }
  .icon svg { width: 10px; height: 10px; }
  .address { margin-top: 12px; }
  /* back */
  .card-back .brand {
    position: absolute; left: 0; right: 0; top: 92px;
    justify-content: center; font-size: 30px; text-align: center;
  }
  .services {
    position: absolute; left: 0; right: 0; top: 200px;
    text-align: center; font-size: 13.5px; line-height: 1.5;
  }
  .bullet { color: var(--orange); margin: 0 6px; }
</style>
</head>
<body>

<section class="card card-front">
  <div class="brand"><span class="brand-dot"></span><span>Northfield Builders Guild</span></div>
  <div class="divider"></div>
  <div class="contact">
    <div class="name">Daniel Hartley</div>
    <div class="title">Managing Director</div>
    <div class="contact-row">
      <span class="icon"><svg viewBox="0 0 10 10"><path d="M2 1l2 2-1 1c.6 1.2 1.8 2.4 3 3l1-1 2 2-1.2 1.2C4.5 9 1 5.5.8 2.2z" fill="#0d0d0d"/></svg></span>
      <span>(555) 014-2290 <span class="office">(Office)</span></span>
    </div>
    <div class="contact-row">
      <span class="icon"><svg viewBox="0 0 10 10"><rect x="2.5" y="0.5" width="5" height="9" rx="1" fill="none" stroke="#0d0d0d" stroke-width="1.2"/></svg></span>
      <span>800-555-0147</span>
    </div>
    <div class="contact-row">
      <span class="icon"><svg viewBox="0 0 10 10"><rect x="1" y="4" width="8" height="4" fill="#0d0d0d"/><rect x="3" y="1" width="4" height="3" fill="#0d0d0d"/></svg></span>
      <span>555.014.0882</span>
    </div>
    <div class="contact-row">
      <span class="icon"><svg viewBox="0 0 10 10"><rect x="1" y="2.5" width="8" height="5" fill="#0d0d0d"/><path d="M1 2.5l4 3 4-3" fill="none" stroke="#ff9900" stroke-width="0.8"/></svg></span>
      <span>support@northfieldguild.org</span>
    </div>
    <div class="address">2400 Ridgeway Ave<br>Suite #210, Northfield, OR 97000</div>
  </div>
</section>

<section class="card card-back">
  <div class="brand"><span class="brand-dot"></span><span>Northfield<br>Builders Guild</span></div>
  <div class="services">
    Business education<span class="bullet">•</span>Assist with business setup and licensing<br>
    Provide safety training<span class="bullet">•</span>Provide a member directory
  </div>
</section>

</body>
</html>
```